Flat bootstrap design for existing site

I'm looking for a modern flat design based around an existing logo. This has to be a custom design (no external templates), and implemented into a bootstrap framework.

The logo is attached as 2 versions - choose whichever you want, that flows better with whatever design you choose.

Added screenshots of the existing site (currently using the default bootstrap layouts). Please make your designs around those pages in the screenshots (i.e. the homepage only has the postal code input and the header). The active page has 3 screenshots, because I wanted to illustrate the other states that would be visible (in the table rows).

This is a moving/junk removal website, just for some context.

Here's some example websites (flat designs) that I like, just to give you an idea of what I'm after.

https://www.plimvora.com/
https://dacklow.com/
https://trevanu.com/
https://quobrintal.com/en/

Coding

Coded - Design and coding required

Number of Pages Required

5+ page

Colors

Designer to choose colors to be used in the design.

Requirements
Must have
• It must be a modern/simple flat design, that is built around the existing logo (attached).
• It has to be implemented using bootstrap.

```html
<!DOCTYPE html>
<html lang="en">
<head>
<meta charset="utf-8">
<title>Tavrel – Booking Details</title>
<link rel="stylesheet" href="https://fonts.googleapis.com/css2?family=Exo+2:wght@400;500;600;700&display=swap">
<style>
  :root {
    --sky: #4ac8f4;
    --sky-deep: #2aa8d6;
    --ink: #555a5e;
    --ink-soft: #6b7075;
    --line: #8a8d90;
    --panel: #f8f8f8;
    --notice: #d0ebf4;
    --table-line: #b9bbbd;
    --pending: #bdbfc0;
    --white: #ffffff;
  }
  * { box-sizing: border-box; margin: 0; padding: 0; }
  html, body { width: 1200px; height: 642px; overflow: hidden; background: var(--white); }
  body { position: relative; font-family: "Exo 2", sans-serif; color: var(--ink); }

  .site-header { position: absolute; left: 0; top: 0; width: 1200px; height: 47px; background: var(--sky); }
  .brand { position: absolute; left: 96px; top: 12px; display: flex; align-items: center; gap: 7px;
    color: var(--white); font-weight: 700; font-size: 21px; letter-spacing: 0.5px; }
  .brand-mark { width: 12px; height: 12px; border-radius: 50%; background: var(--white); }
  .main-nav a { position: absolute; top: 0; height: 47px; line-height: 47px; color: var(--white);
    text-decoration: none; font-weight: 600; font-size: 13.5px; }
  .nav-book { left: 626px; }
  .nav-how { left: 692px; }
  .nav-driver { left: 794px; width: 135px; text-align: center; background: var(--sky-deep); }
  .nav-account { left: 942px; }
  .caret { display: inline-block; margin-left: 6px; border-left: 4px solid transparent;
    border-right: 4px solid transparent; border-top: 5px solid var(--white); vertical-align: 2px; }

  .booking-panel { position: absolute; left: 185px; top: 84px; width: 830px; height: 236px;
    background: var(--panel); border-radius: 4px; }
  .panel-title { position: absolute; left: 48px; top: 22px; font-size: 14.5px; font-weight: 500; }
  .field-label { position: absolute; font-size: 12.5px; color: var(--ink-soft); }
  .field-box { position: absolute; border: 1px solid var(--line); background: var(--panel);
    font-size: 9px; color: var(--ink-soft); padding: 0 13px; display: flex; align-items: center; }
  .label-package { left: 47px; top: 54px; }
  .box-package { left: 43px; top: 80px; width: 291px; height: 24px; }
  .label-pickup { left: 417px; top: 53px; }
  .box-pickup { left: 409px; top: 80px; width: 262px; height: 24px; padding-left: 18px; }
  .calendar-btn { position: absolute; left: 670px; top: 80px; width: 29px; height: 24px;
    background: var(--sky-deep); display: flex; align-items: center; justify-content: center; }
  .label-description { left: 47px; top: 117px; }
  .box-description { left: 43px; top: 141px; width: 661px; height: 41px; align-items: flex-start;
    padding: 5px 4px; }
  .update-btn { position: absolute; left: 39px; top: 194px; width: 131px; height: 28px; border: none;
    border-radius: 14px; background: var(--sky); color: var(--white); font-family: "Exo 2", sans-serif;
    font-size: 15px; font-weight: 600; letter-spacing: 0.5px; box-shadow: 0 2px 0 var(--sky-deep); }

  .drivers-title { position: absolute; left: 213px; top: 349px; font-size: 14.5px; font-weight: 500; }
  .drivers-notice { position: absolute; left: 206px; top: 379px; width: 787px; height: 24px;
    background: var(--notice); font-size: 9px; color: var(--ink-soft); line-height: 24px; padding-left: 28px; }

  .drivers-table { position: absolute; left: 207px; top: 423px; width: 786px; height: 162px;
    border: 1px solid var(--table-line); font-size: 9.5px; }
  .table-head { position: absolute; left: 0; top: 0; width: 100%; height: 29px;
    border-bottom: 1px solid #dcdcdc; font-weight: 500; font-size: 10px; }
  .table-head span, .driver-row span { position: absolute; }
  .table-head span { top: 11px; }
  .col-name { left: 30px; }
  .col-distance { left: 180px; }
  .table-head .col-distance { left: 183px; }
  .col-time { left: 348px; }
  .driver-row .col-time { left: 392px; }
  .driver-row { position: absolute; left: 0; width: 100%; height: 22px; color: var(--ink); }
  .driver-row span { top: 3px; }
  .status-pending { position: absolute; left: 650px; top: 2px; width: 107px; height: 19px;
    background: var(--pending); border: 1px solid #a9abac; color: var(--white); font-size: 9.5px;
    text-align: center; line-height: 17px; }
  .row-1 { top: 35px; }
  .row-2 { top: 69px; }
  .row-3 { top: 104px; }
  .row-4 { top: 138px; }

  .site-footer { position: absolute; left: 0; top: 612px; width: 1200px; height: 30px;
    background: var(--sky); color: var(--white); font-size: 10.5px; font-weight: 600;
    text-align: center; line-height: 30px; }
</style>
</head>
<body>
  <header class="site-header">
    <div class="brand"><span class="brand-mark"></span>TAVREL</div>
    <nav class="main-nav">
      <a class="nav-book" href="#">Book</a>
      <a class="nav-how" href="#">How It Works</a>
      <a class="nav-driver" href="#">Become A Driver</a>
      <a class="nav-account" href="#">george@mailvento.com<span class="caret"></span></a>
    </nav>
  </header>

  <section class="booking-panel">
    <h2 class="panel-title">Booking Details</h2>
    <div class="field-label label-package">Package Selected :</div>
    <div class="field-box box-package">Package 1</div>
    <div class="field-label label-pickup">Pick-up time selected :</div>
    <div class="field-box box-pickup">July 18 at 4:13 am</div>
    <div class="calendar-btn">
      <svg width="11" height="11" viewBox="0 0 11 11" aria-hidden="true">
        <rect x="0.5" y="1.5" width="10" height="9" fill="none" stroke="#fff"/>
        <rect x="0.5" y="1.5" width="10" height="2" fill="#fff"/>
        <g fill="#fff"><rect x="2" y="5" width="1.5" height="1.5"/><rect x="4.75" y="5" width="1.5" height="1.5"/><rect x="7.5" y="5" width="1.5" height="1.5"/><rect x="2" y="7.5" width="1.5" height="1.5"/><rect x="4.75" y="7.5" width="1.5" height="1.5"/><rect x="7.5" y="7.5" width="1.5" height="1.5"/></g>
      </svg>
    </div>
    <div class="field-label label-description">Description :</div>
    <div class="field-box box-description">1 large stove</div>
    <button class="update-btn">UPDATE</button>
  </section>

  <h2 class="drivers-title">Drivers In Your Area</h2>
  <div class="drivers-notice">Please stay on this page and be patient, while we contact the drivers and find you one ASAP</div>

  <div class="drivers-table">
    <div class="table-head">
      <span class="col-name">Name</span>
      <span class="col-distance">Distance (km)</span>
      <span class="col-time">Agreed Pick-Up Time</span>
    </div>
    <div class="driver-row row-1">
      <span class="col-name">Harlan Mote</span><span class="col-distance">4.04km away</span><span class="col-time">–</span>
      <div class="status-pending">Pending</div>
    </div>
    <div class="driver-row row-2">
      <span class="col-name">Thomas Kellar</span><span class="col-distance">5.6km away</span><span class="col-time">–</span>
      <div class="status-pending">Pending</div>
    </div>
    <div class="driver-row row-3">
      <span class="col-name">Edric Vanlow</span><span class="col-distance">11.13km away</span><span class="col-time">–</span>
      <div class="status-pending">Pending</div>
    </div>
    <div class="driver-row row-4">
      <span class="col-name">Vance Juliard</span><span class="col-distance">11.81km away</span><span class="col-time">–</span>
      <div class="status-pending">Pending</div>
    </div>
  </div>

  <footer class="site-footer">© 2017 Tavrel. All Rights Reserved.</footer>
</body>
</html>
```